General contractor/GM consaltant business card

I need a card for my contracting company in North Dakota, we build industrial buildings for the oil feild and oil feild related companies offices, shops, airplain hangars, airports ext. We have a familly atmosphere on the job and are very relational and personal.
Industry/Entity Type
Industrial
Contact Information for Business Card
Ridgepost Contractors LLC.
Derek T.Holloway
4837 Tamarind dr. Colorado Springs, CO. 80917
Cell# 406-555-0148
derek@ridgepostcontractors.com

```html
<!DOCTYPE html>
<html lang="en">
<head>
<meta charset="utf-8">
<title>Ridgepost Contractors LLC. – Business Card</title>
<link rel="stylesheet" href="https://fonts.googleapis.com/css2?family=Arimo:wght@400&display=swap">
<style>
  :root {
    --stage: #e9e7e4;
    --paper: #ffffff;
    --paper-edge: #dcdcdc;
    --brand-red: #e0262f;
    --brand-blue: #2158a8;
    --blue-light: #5b8bd0;
    --ink: #2c4f9a;
  }
  * { margin: 0; padding: 0; box-sizing: border-box; }
  html, body { width: 1200px; height: 858px; overflow: hidden; }
  body {
    background: var(--stage);
    font-family: "Arimo", Arial, sans-serif;
    position: relative;
  }
  .card {
    position: absolute;
    width: 525px;
    height: 300px;
    background: var(--paper);
    border: 1px solid var(--paper-edge);
    box-shadow: 0 6px 18px rgba(0,0,0,0.12);
    overflow: hidden;
  }
  .card--front { left: 50px; top: 279px; }
  .card--back { left: 625px; top: 279px; }

  /* Front */
  .name-rule {
    position: absolute;
    left: 0; right: 0; top: 70px;
    height: 2px;
    background: var(--brand-blue);
  }
  .person-name {
    position: absolute;
    top: 58px; right: 150px;
    padding: 0 8px;
    background: var(--paper);
    color: var(--brand-red);
    font-size: 20px;
    line-height: 24px;
  }
  .contact-list {
    position: absolute;
    left: 36px; top: 172px;
    list-style: none;
  }
  .contact-item {
    display: flex;
    align-items: center;
    gap: 12px;
    color: var(--ink);
    font-size: 15px;
    line-height: 27px;
  }
  .contact-icon { width: 14px; height: 14px; flex: none; }
  .mountain-art {
    position: absolute;
    right: 0; top: 0;
    width: 120px; height: 100%;
    background: linear-gradient(90deg, rgba(33,88,168,0) 0%, rgba(33,88,168,0.35) 55%, var(--brand-blue) 100%);
  }

  /* Back */
  .brand-block {
    position: absolute;
    inset: 0;
    display: flex;
    align-items: center;
    justify-content: center;
    gap: 12px;
  }
  .brand-dot {
    width: 14px; height: 14px;
    border-radius: 50%;
    background: var(--brand-red);
  }
  .brand-name {
    color: var(--brand-red);
    font-size: 30px;
    line-height: 36px;
  }
</style>
</head>
<body>
  <section class="card card--front" aria-label="Business card front">
    <div class="name-rule"></div>
    <p class="person-name">Derek T.Holloway</p>
    <ul class="contact-list">
      <li class="contact-item">
        <svg class="contact-icon" viewBox="0 0 16 16" aria-hidden="true">
          <path fill="#e0262f" d="M3 2h3l1.5 3.5-2 1.2a8 8 0 0 0 3.8 3.8l1.2-2L14 10v3a1 1 0 0 1-1 1A11 11 0 0 1 2 3a1 1 0 0 1 1-1z"/>
        </svg>
        <span>406-555-0148</span>
      </li>
      <li class="contact-item">
        <svg class="contact-icon" viewBox="0 0 16 16" aria-hidden="true">
          <path fill="#e0262f" d="M8 1a5 5 0 0 0-5 5c0 4 5 9 5 9s5-5 5-9a5 5 0 0 0-5-5zm0 7a2 2 0 1 1 0-4 2 2 0 0 1 0 4z"/>
        </svg>
        <span>4837 Tamarind dr. Colorado Springs, CO. 80917</span>
      </li>
      <li class="contact-item">
        <svg class="contact-icon" viewBox="0 0 16 16" aria-hidden="true">
          <rect x="1" y="3" width="14" height="10" fill="#e0262f"/>
          <path d="M1.5 3.5 8 9l6.5-5.5" fill="none" stroke="#fff" stroke-width="1.3"/>
        </svg>
        <span>derek@ridgepostcontractors.com</span>
      </li>
    </ul>
    <div class="mountain-art" role="img" aria-label="Blue mountain ridge illustration along the card edge"></div>
  </section>

  <section class="card card--back" aria-label="Business card back">
    <div class="brand-block">
      <span class="brand-dot" aria-hidden="true"></span>
      <span class="brand-name">Ridgepost Contractors LLC.</span>
    </div>
  </section>
</body>
</html>
```